Web design for a honey company

We are a honey retailing company currently looking for creative design for 3 pages of our existing e-commerce website which can be found here www.alpha.tolvenmarsk.co.nz. The designs need to be responsive i.e. presented in both desktop and mobile versions. We want to use the existing page color pallet, however any fonts can be used. Please use the texts and graphic content in the attachment files provided. For more detailed instructions please. The page does not require coding, the output files should be provided as layered and editable PSD.<br/><br/>Task 2: design 2 home page banners. Images, texts and the concept provided in the "layout structure" file. <br/><br/>The web designs should be presented in both desktop and mobile versions. We are looking for professional designer submissions only!

Target Market(s)

Hi-end consumers
Health conscious consumers

Number of Pages Required

3 page

Requirements
Must have
• 50% of images supplied along + any suggested stock images.
• Supplied texts integrated in the designs.
• Please only use the product images we have provided!
Should not have
• Clipart vector bees, vector honey slots or combs.
• No images of honey in glass jars!
• Do not use images of the traditional honey wooden spoons!
• Do not use images of any other but Manuka flower!

```html
<!DOCTYPE html>
<html lang="en">
<head>
<meta charset="utf-8">
<title>Tolvenmarsk – About us (desktop and mobile)</title>
<link rel="stylesheet" href="https://fonts.googleapis.com/css2?family=Lato:wght@400;700&family=Tinos&display=swap">
<style>
  :root{
    --canvas:#cbcbcb;
    --ink:#0b0b12;
    --footer:#1d1d1d;
    --footer-bar:#0c0c0c;
    --page:#f4f4f4;
    --gold:#d8b45a;
    --gold-light:#f1d98f;
    --heading:#1f1f1f;
    --body:#7a7a7a;
    --white:#ffffff;
    --menu:rgba(150,150,160,.82);
  }
  *{margin:0;padding:0;box-sizing:border-box}
  html,body{width:1200px;height:1200px;overflow:hidden;background:var(--canvas)}
  body{position:relative;font-family:"Lato",sans-serif;color:var(--body)}
  .screen{position:absolute;top:50px;height:1098px;background:var(--page);overflow:hidden}
  .screen--desktop{left:206px;width:506px}
  .screen--mobile{left:748px;width:155px}
  .abs{position:absolute}

  /* header */
  .site-header{position:absolute;left:0;top:0;width:100%;background:var(--ink)}
  .gold-rule{position:absolute;left:0;width:100%;background:linear-gradient(90deg,#b8913a,var(--gold-light) 50%,#b8913a)}
  .nav-link{position:absolute;font-size:4.4px;color:var(--white);white-space:nowrap}
  .nav-link--active{color:var(--gold)}
  .brand{position:absolute;display:flex;align-items:center;justify-content:center;background:var(--ink);border-radius:3px;color:var(--gold);font-family:"Tinos",serif;letter-spacing:.6px}
  .dropdown{position:absolute;left:297px;top:35px;width:99px;height:64px;background:var(--menu)}
  .dropdown span{position:absolute;left:9px;font-size:4.2px;color:var(--white)}

  /* hero */
  .hero{position:absolute;left:0;width:100%;background:linear-gradient(180deg,#e7e8ea 0%,#dfe2e6 40%,#e3e6dc 75%,#e8eadf 100%)}
  .hero-title{position:absolute;left:0;width:100%;text-align:center;font-family:"Tinos",serif;color:#151515;letter-spacing:.5px}

  /* content */
  .section-title{position:absolute;font-family:"Tinos",serif;color:var(--heading);white-space:nowrap;letter-spacing:.2px}
  .bee-mark{position:absolute;width:10px;height:7px;background:var(--gold);opacity:.55;border-radius:3px}
  .copy{position:absolute;font-size:4.5px;line-height:7.5px;color:var(--body)}
  .copy p{margin-bottom:7.5px}
  .photo-frame{position:absolute;background:var(--white);box-shadow:0 1px 6px rgba(0,0,0,.15)}
  .photo{position:absolute}
  .photo--apiary{background:linear-gradient(180deg,#6f9a4a 0%,#86ad55 45%,#c9d3da 62%,#7fa04a 80%,#5f8c3a 100%)}
  .photo--hive{background:linear-gradient(100deg,#c9cbcf 0%,#9ea3a8 25%,#4a3c25 45%,#7d9c58 65%,#b8c3c9 85%,#d5d8da 100%)}
  .bird-card{position:absolute;background:var(--white)}
  .bird-art{position:absolute;inset:0}
  .bird-art--kotare{background:linear-gradient(160deg,#ffffff 10%,#6ec1ea 45%,#2f6fc4 75%,#ffffff 95%)}
  .bird-art--kereru{background:linear-gradient(160deg,#ffffff 10%,#9fd3b0 35%,#7a3c95 65%,#ffffff 95%)}
  .bird-art--pukeko{background:linear-gradient(160deg,#ffffff 15%,#3b47b8 50%,#e48aa0 85%,#ffffff 100%)}
  .bird-art--tui{background:linear-gradient(160deg,#ffffff 10%,#2d8f9a 45%,#1f4f63 65%,#f2c22c 85%,#ffffff 100%)}
  .bird-name{position:absolute;font-family:"Tinos",serif;color:var(--heading)}
  .bird-copy{position:absolute;font-size:4.2px;line-height:7.5px;color:var(--body)}

  /* footer */
  .site-footer{position:absolute;left:0;width:100%;background:var(--footer)}
  .footer-bar{position:absolute;left:0;width:100%;background:var(--footer-bar);color:var(--white);text-align:center}
  .footer-links{position:absolute;list-style:none;color:var(--white)}
  .pay-tile{position:absolute;background:#e9e9ec;border-radius:1.5px}
  .pay-tile--b{background:#3d7fbf}
  .follow-title{position:absolute;font-family:"Tinos",serif;color:var(--white);white-space:nowrap}
  .social{position:absolute;border:.7px solid var(--white);border-radius:50%}

  /* mobile sizes */
  .screen--mobile .copy{font-size:2.5px;line-height:4.4px}
  .screen--mobile .copy p{margin-bottom:4px}
  .screen--mobile .bird-copy{font-size:2.3px;line-height:4.2px}
  .burger{position:absolute;left:137px;width:9px;height:.9px;background:var(--white)}
</style>
</head>
<body>

<!-- DESKTOP -->
<section class="screen screen--desktop" aria-label="About us page, desktop">
  <div class="hero" style="top:37px;height:138px" role="img" aria-label="Faded photo of beehives in a green field"></div>
  <h1 class="hero-title" style="top:90px;font-size:22px">ABOUT US</h1>
  <div class="gold-rule" style="top:175px;height:5px"></div>

  <header class="site-header" style="height:34px">
    <span class="nav-link" style="left:142px;top:21px">Shop ▾</span>
    <span class="nav-link" style="left:168px;top:21px">MGO Manuka honey ▾</span>
    <span class="nav-link nav-link--active" style="left:297px;top:21px">About us ▾</span>
    <span class="nav-link" style="left:330px;top:21px">Contact us ▾</span>
    <svg class="abs" style="left:418px;top:6px" width="9" height="9" viewBox="0 0 10 10" fill="none" stroke="#fff" stroke-width="1"><circle cx="5" cy="3.3" r="2.2"/><path d="M1 9.5c0-2.5 1.8-3.8 4-3.8s4 1.3 4 3.8"/></svg>
    <span class="nav-link nav-link--active" style="left:428px;top:8px">Login</span>
    <svg class="abs" style="left:443px;top:6px" width="9" height="8" viewBox="0 0 10 9" fill="none" stroke="#fff" stroke-width="1"><path d="M5 8.3L1.3 4.6A2.2 2.2 0 015 1.8a2.2 2.2 0 013.7 2.8z"/></svg>
    <svg class="abs" style="left:463px;top:5px" width="10" height="9" viewBox="0 0 11 10" fill="none" stroke="#fff" stroke-width="1"><path d="M.5 .8h2l1.4 5.7h5.4l1.2-4H3"/><circle cx="4.5" cy="8.6" r=".8"/><circle cx="8.5" cy="8.6" r=".8"/></svg>
  </header>
  <div class="gold-rule" style="top:34px;height:3px"></div>
  <div class="brand" style="left:223px;top:16px;width:60px;height:34px;font-size:6px">TOLVENMARSK</div>

  <nav class="dropdown" aria-label="About us menu">
    <span style="top:8px">our story</span>
    <span style="top:27px">our philosophy</span>
    <span style="top:46px">Our labels (birds)</span>
  </nav>
  <svg class="abs" style="left:307px;top:25px" width="6" height="8" viewBox="0 0 6 8"><path d="M.5.5v6l1.6-1.5 1.2 2.6 1-.5-1.2-2.5h2.2z" fill="#fff" stroke="#000" stroke-width=".5"/></svg>

  <h2 class="section-title" style="left:31px;top:212px;font-size:11px">OUR STORY</h2>
  <div class="bee-mark" role="img" aria-label="Small gold bee ornament" style="left:31px;top:233px"></div>
  <div class="copy" style="left:31px;top:255px;width:218px">
    <p>At Tolvenmarsk, we're passionate about sharing the wonders of New Zealand's honey with our discerning customers around the world. Our company was founded on the principles of providing great products with great service in an environmentally responsible way.</p>
    <p>Our honey is gathered from hives in the most pristine areas of New Zealand, with minimal processing and impact to the nature. Honey is extracted from the hives in a way to ensure minimal disruption to the bees, and processed with no additives – with honey this good, we don't need them.</p>
    <p>Along with producing great quality products, our team is also focused on providing our customers with great service. New Zealanders are known for their exceptional service skills, and we're proud to put these to use for our customers around the world.</p>
  </div>
  <div class="photo-frame" style="left:264px;top:209px;width:210px;height:133px">
    <div class="photo photo--apiary" style="left:5px;top:5px;width:200px;height:123px" role="img" aria-label="Beekeepers in suits carrying frames between blue hives on grass"></div>
  </div>

  <div class="photo-frame" style="left:32px;top:379px;width:210px;height:133px">
    <div class="photo photo--hive" style="left:5px;top:5px;width:200px;height:123px" role="img" aria-label="Beekeeper lifting a frame covered in bees beside a smoker"></div>
  </div>
  <h2 class="section-title" style="left:254px;top:382px;font-size:11px">OUR PHILOSOPHY - THE NATURAL WAY.</h2>
  <div class="bee-mark" role="img" aria-label="Small gold bee ornament" style="left:254px;top:403px"></div>
  <div class="copy" style="left:254px;top:425px;width:218px">
    <p>Here at Tolvenmarsk, we work as hard as our bees to make sure that the honey you get is exactly as it was when the bees finished making it and sealed it in its honeycomb cell.</p>
    <p>And to ensure that we can provide you with the best honey, we need to make sure that our bees, and the environment they live in, are protected. Bees are a vital part of our ecosystem – without them, humanity may not survive. So it's no exaggeration when we say that the bees are the most important part of our business, and that we make sure that they are placed in the best environments with the best beekeepers to look after them.</p>
    <p>Tolvenmarsk Honey is made by nature and harvested for you. Nothing added, nothing taken away. Just 100% natural Manuka honey.</p>
  </div>

  <h2 class="section-title" style="left:31px;top:552px;font-size:11px">OUR LABELS (THE BIRDS)</h2>
  <div class="bee-mark" role="img" aria-label="Small gold bee ornament" style="left:31px;top:574px"></div>
  <div class="copy" style="left:31px;top:595px;width:442px">
    <p>New Zealand's natural environment is like no other. As well as having unique plants, like the Manuka tree, we also have many beautiful native birds. We're proud to share our honey with the world in jars adorned by some of these birds.</p>
    <p>They're drawn by artist Marta Rennick, who is known by the name SmallFern. Marta grew up in rural New Zealand and her artwork reflects her love of nature, simplicity and colour.<br>If you're not familiar with New Zealand's birds, here's a little bit more about those that you'll see on our jars.</p>
  </div>

  <div class="bird-card" style="left:32px;top:671px;width:94px;height:94px"><div class="bird-art bird-art--kotare" role="img" aria-label="Low-poly illustration of a kōtare kingfisher on a branch"></div></div>
  <div class="bird-card" style="left:147px;top:671px;width:94px;height:94px"><div class="bird-art bird-art--kereru" role="img" aria-label="Low-poly illustration of a kererū wood pigeon"></div></div>
  <div class="bird-card" style="left:263px;top:671px;width:94px;height:94px"><div class="bird-art bird-art--pukeko" role="img" aria-label="Low-poly illustration of a pūkeko swamphen"></div></div>
  <div class="bird-card" style="left:379px;top:671px;width:94px;height:94px"><div class="bird-art bird-art--tui" role="img" aria-label="Low-poly illustration of a tūī on a flowering branch"></div></div>

  <h3 class="bird-name" style="left:32px;top:786px;font-size:11px">KŌTARE</h3>
  <h3 class="bird-name" style="left:148px;top:786px;font-size:11px">KERERŪ</h3>
  <h3 class="bird-name" style="left:263px;top:786px;font-size:11px">PŪKEKO</h3>
  <h3 class="bird-name" style="left:379px;top:786px;font-size:11px">TŪĪ</h3>
  <p class="bird-copy" style="left:32px;top:806px;width:87px">The kōtare is our native kingfisher and appears on our Manuka honey label. You'll see their beautiful green/blue feathers shine in the sunlight as they sit on a branch waiting for their next meal. They live all over New Zealand in a wide range of habitats.</p>
  <p class="bird-copy" style="left:148px;top:806px;width:87px">The kererū is a wood pigeon, also known as a kūkū or kūkupa. They're only found in New Zealand and you'll see them on our rewarewa honey jars. If you're in the forest, you may hear them before you see them, with their heavy wing beats. But you'll be dazzled by their beautiful, colourful plummage when you do spot them sitting peacefully in a tree above you.</p>
  <p class="bird-copy" style="left:264px;top:806px;width:87px">The pūkeko can be found all over New Zealand and looks great on our Manuka blend honey. Their brilliant red beaks and frontal shields (the bit on the top of their heads), along with their big feet, long legs and purple chest make them striking characters. They're also known by the less glamourous name of the purple swamphen but they live in a range of habitats.</p>
  <p class="bird-copy" style="left:380px;top:806px;width:87px">Tūī are much like our honey bees - they love the nectar from our native flowers. You'll recognise tūī by the bright white tuft on their chest. From a distance, the rest of their plummage looks black but if you look closer, you'll find it's got a beautiful green/blue sheen to it. As a lover of many different nectars, it's only right for the tūī to represent our multiflora honey.</p>

  <footer class="site-footer" style="top:960px;height:124px">
    <ul class="footer-links" style="left:33px;top:45px;font-size:4.4px;line-height:9.5px">
      <li>Shop Manuka honey</li><li>Shop Native honey</li><li>About us</li><li>Contacts</li>
    </ul>
    <ul class="footer-links" style="left:130px;top:45px;font-size:4.4px;line-height:9.5px">
      <li>Terms &amp; Conditions</li><li>Privacy Policy</li><li>Returns policy</li><li>FAQs</li><li>Partnership enquiries</li>
    </ul>
    <div class="pay-tile" style="left:238px;top:58px;width:28px;height:16px" role="img" aria-label="Payment option"></div>
    <div class="pay-tile pay-tile--b" style="left:270px;top:58px;width:28px;height:16px" role="img" aria-label="Payment option"></div>
    <div class="pay-tile" style="left:302px;top:58px;width:28px;height:16px" role="img" aria-label="Payment option"></div>
    <h4 class="follow-title" style="left:387px;top:41px;font-size:8.5px">FOLLOW US</h4>
    <div class="social" style="left:387px;top:62px;width:12px;height:12px"></div>
    <div class="social" style="left:405px;top:62px;width:12px;height:12px"></div>
    <div class="social" style="left:423px;top:62px;width:12px;height:12px"></div>
    <div class="social" style="left:441px;top:62px;width:12px;height:12px"></div>
    <div class="social" style="left:459px;top:62px;width:12px;height:12px"></div>
  </footer>
  <div class="gold-rule" style="top:955px;height:5px"></div>
  <div class="brand" style="left:213px;top:935px;width:80px;height:46px;font-size:8px">TOLVENMARSK</div>
  <div class="footer-bar" style="top:1084px;height:14px;font-size:4.4px;line-height:14px">Copyright © 2020 Tolvenmarsk Health Limited. All Right Reserved.</div>
</section>

<!-- MOBILE -->
<section class="screen screen--mobile" aria-label="About us page, mobile">
  <div class="hero" style="top:18px;height:91px" role="img" aria-label="Faded photo of beehives in a green field"></div>
  <h1 class="hero-title" style="top:53px;font-size:12.5px">ABOUT US</h1>
  <div class="gold-rule" style="top:109px;height:3px"></div>

  <header class="site-header" style="height:15px">
    <span class="burger" style="top:5px"></span>
    <span class="burger" style="top:7.5px;left:139px;width:7px"></span>
    <span class="burger" style="top:10px"></span>
  </header>
  <div class="gold-rule" style="top:15px;height:2px"></div>
  <div class="brand" style="left:57px;top:4px;width:40px;height:22px;font-size:4.2px;letter-spacing:.3px">TOLVENMARSK</div>

  <div class="photo-frame" style="left:8px;top:130px;width:138px;height:88px">
    <div class="photo photo--apiary" style="left:3px;top:3px;width:132px;height:82px" role="img" aria-label="Beekeepers in suits carrying frames between blue hives on grass"></div>
  </div>
  <h2 class="section-title" style="left:7.5px;top:232px;font-size:7px">OUR STORY</h2>
  <div class="bee-mark" role="img" aria-label="Small gold bee ornament" style="left:7.5px;top:246px;width:6px;height:4.5px"></div>
  <div class="copy" style="left:7.5px;top:258px;width:141px">
    <p>At Tolvenmarsk, we're passionate about sharing the wonders of New Zealand's honey with our discerning customers around the world. Our company was founded on the principles of providing great products with great service in an environmentally responsible way.</p>
    <p>Our honey is gathered from hives in the most pristine areas of New Zealand, with minimal processing and impact to the nature. Honey is extracted from the hives in a way to ensure minimal disruption to the bees, and processed with no additives – with honey this good, we don't need them.</p>
    <p>Along with producing great quality products, our team is also focused on providing our customers with great service. New Zealanders are known for their exceptional service skills, and we're proud to put these to use for our customers around the world.</p>
  </div>

  <div class="photo-frame" style="left:8px;top:333px;width:138px;height:85px">
    <div class="photo photo--hive" style="left:3px;top:3px;width:132px;height:79px" role="img" aria-label="Beekeeper lifting a frame covered in bees beside a smoker"></div>
  </div>
  <h2 class="section-title" style="left:7.5px;top:433px;font-size:7px">OUR PHILOSOPHY - THE NATURAL WAY.</h2>
  <div class="bee-mark" role="img" aria-label="Small gold bee ornament" style="left:7.5px;top:446px;width:6px;height:4.5px"></div>
  <div class="copy" style="left:7.5px;top:459px;width:141px">
    <p>Here at Tolvenmarsk, we work as hard as our bees to make sure that the honey you get is exactly as it was when the bees finished making it and sealed it in its honeycomb cell.</p>
    <p>And to ensure that we can provide you with the best honey, we need to make sure that our bees, and the environment they live in, are protected. Bees are a vital part of our ecosystem – without them, humanity may not survive. So it's no exaggeration when we say that the bees are the most important part of our business, and that we make sure that they are placed in the best environments with the best beekeepers to look after them.</p>
    <p>Tolvenmarsk Honey is made by nature and harvested for you. Nothing added, nothing taken away. Just 100% natural Manuka honey.</p>
  </div>

  <h2 class="section-title" style="left:7.5px;top:532px;font-size:7px">OUR LABELS (THE BIRDS)</h2>
  <div class="bee-mark" role="img" aria-label="Small gold bee ornament" style="left:7.5px;top:545px;width:6px;height:4.5px"></div>
  <div class="copy" style="left:8px;top:558px;width:139px">
    <p>New Zealand's natural environment is like no other. As well as having unique plants, like the Manuka tree, we also have many beautiful native birds. We're proud to share our honey with the world in jars adorned by some of these birds.</p>
    <p>They're drawn by artist Marta Rennick, who is known by the name SmallFern. Marta grew up in rural New Zealand and her artwork reflects her love of nature, simplicity and colour. If you're not familiar with New Zealand's birds, here's a little bit more about those that you'll see on our jars.</p>
  </div>

  <div class="bird-card" style="left:9px;top:618px;width:61px;height:61px"><div class="bird-art bird-art--kotare" role="img" aria-label="Low-poly illustration of a kōtare kingfisher on a branch"></div></div>
  <div class="bird-card" style="left:84px;top:618px;width:61px;height:61px"><div class="bird-art bird-art--kereru" role="img" aria-label="Low-poly illustration of a kererū wood pigeon"></div></div>
  <h3 class="bird-name" style="left:8.5px;top:692px;font-size:7px">KŌTARE</h3>
  <h3 class="bird-name" style="left:84px;top:692px;font-size:7px">KERERŪ</h3>
  <p class="bird-copy" style="left:8.5px;top:705px;width:56px">The kōtare is our native kingfisher and appears on our Manuka honey label. You'll see their beautiful green/blue feathers shine in the sunlight as they sit on a branch waiting for their next meal. They live all over New Zealand in a wide range of habitats.</p>
  <p class="bird-copy" style="left:84px;top:705px;width:56px">The kererū is a wood pigeon, also known as a kūkū or kūkupa. They're only found in New Zealand and you'll see them on our rewarewa honey jars. If you're in the forest, you may hear them before you see them, with their heavy wing beats. But you'll be dazzled by their beautiful colourful plummage when you do spot them sitting peacefully in a tree above you.</p>

  <div class="bird-card" style="left:9px;top:766px;width:61px;height:61px"><div class="bird-art bird-art--pukeko" role="img" aria-label="Low-poly illustration of a pūkeko swamphen"></div></div>
  <div class="bird-card" style="left:84px;top:766px;width:61px;height:61px"><div class="bird-art bird-art--tui" role="img" aria-label="Low-poly illustration of a tūī on a flowering branch"></div></div>
  <h3 class="bird-name" style="left:8.5px;top:841px;font-size:7px">PŪKEKO</h3>
  <h3 class="bird-name" style="left:84px;top:841px;font-size:7px">TŪĪ</h3>
  <p class="bird-copy" style="left:8.5px;top:853px;width:56px">The pūkeko can be found all over New Zealand and looks great on our Manuka blend honey. Their brilliant red beaks and frontal shields (the bit on the top of their heads), along with their big feet, long legs and purple chest make them striking characters. They're also known by the less glamourous name of the purple swamphen but they live in a range of habitats.</p>
  <p class="bird-copy" style="left:84px;top:853px;width:56px">Tūī are much like our honey bees - they love the nectar from our native flowers. You'll recognise tūī by the bright white tuft on their chest. From a distance, the rest of their plummage looks black but if you look closer, you'll find it's got a beautiful green/blue sheen to it. As a lover of many different nectars, it's only right for the tūī to represent our multiflora honey.</p>

  <footer class="site-footer" style="top:937px;height:151px">
    <ul class="footer-links" style="left:7.5px;top:24px;font-size:2.9px;line-height:6.2px">
      <li>Shop Manuka honey</li><li>Shop Native honey</li><li>About us</li><li>Contacts</li>
    </ul>
    <ul class="footer-links" style="left:7.5px;top:51px;font-size:2.9px;line-height:6.2px">
      <li>Terms &amp; Conditions</li><li>Privacy Policy</li><li>Returns policy</li><li>FAQs</li><li>Partnership enquiries</li>
    </ul>
    <div class="pay-tile" style="left:7.5px;top:94px;width:18px;height:10px" role="img" aria-label="Payment option"></div>
    <div class="pay-tile pay-tile--b" style="left:28px;top:94px;width:18px;height:10px" role="img" aria-label="Payment option"></div>
    <div class="pay-tile" style="left:49px;top:94px;width:18px;height:10px" role="img" aria-label="Payment option"></div>
    <h4 class="follow-title" style="left:7.5px;top:120px;font-size:5.5px">FOLLOW US</h4>
    <div class="social" style="left:7.5px;top:133px;width:6px;height:6px"></div>
    <div class="social" style="left:16.5px;top:133px;width:6px;height:6px"></div>
    <div class="social" style="left:25.5px;top:133px;width:6px;height:6px"></div>
    <div class="social" style="left:34.5px;top:133px;width:6px;height:6px"></div>
    <div class="social" style="left:43.5px;top:133px;width:6px;height:6px"></div>
  </footer>
  <div class="gold-rule" style="top:934px;height:3px"></div>
  <div class="brand" style="left:51px;top:920px;width:53px;height:30px;font-size:5.2px;letter-spacing:.3px">TOLVENMARSK</div>
  <div class="footer-bar" style="top:1088px;height:10px;font-size:2.5px;line-height:10px">Copyright © 2020 Tolvenmarsk Health Limited. All Right Reserved.</div>
</section>

</body>
</html>
```